Investment company needing business card

We are wanting a business card which looks sharp and easy on the eye. We are thinking of having a business card with the logo embossed on it, to really make it stand out. We will only have a small amount of information of the business card, person's name, position, email address and phone number

Contact Information for Business Card

Danielle Frost
Executive Assistant
+64 21 473 5162
danielf@harwickpartners.co.nz

Requirements
Must have
• Embossed logo
Should not have
• Not to be busy

```html
<!DOCTYPE html>
<html lang="en">
<head>
<meta charset="utf-8">
<title>Harwick Partners — Business Card</title>
<link rel="stylesheet" href="https://fonts.googleapis.com/css2?family=Exo+2:wght@700&family=Lato:wght@400&display=swap">
<style>
  :root {
    --backdrop: #747474;
    --card: #1c1b1c;
    --accent: #22b86b;
    --text-light: #c9c9c9;
  }
  * { margin: 0; padding: 0; box-sizing: border-box; }
  html, body { width: 1200px; height: 802px; overflow: hidden; }
  body { background: var(--backdrop); position: relative; }

  .card {
    position: absolute;
    top: 274px;
    width: 445px;
    height: 265px;
    background: var(--card);
  }
  .card--front { left: 134px; }
  .card--back { left: 624px; }

  .brand {
    position: absolute;
    display: flex;
    align-items: center;
    gap: 9px;
    font-family: "Exo 2", sans-serif;
    font-weight: 700;
    color: var(--accent);
    letter-spacing: 0.02em;
    white-space: nowrap;
  }
  .brand__square {
    display: block;
    background: var(--accent);
    flex: none;
  }
  .card--front .brand { right: 26px; top: 66px; font-size: 21px; }
  .card--front .brand__square { width: 38px; height: 38px; }
  .card--back .brand { left: 50%; top: 50%; transform: translate(-50%, -50%); font-size: 27px; }
  .card--back .brand__square { width: 50px; height: 50px; }

  .contact-bar {
    position: absolute;
    left: 0;
    top: 153px;
    width: 8px;
    height: 89px;
    background: var(--accent);
  }
  .contact {
    position: absolute;
    left: 28px;
    top: 155px;
  }
  .contact__name {
    font-family: "Exo 2", sans-serif;
    font-weight: 700;
    font-size: 17px;
    color: var(--accent);
    letter-spacing: 0.02em;
    line-height: 1.1;
  }
  .contact__role {
    font-family: "Lato", sans-serif;
    font-size: 12.5px;
    color: var(--text-light);
    margin-top: 1px;
  }
  .contact__list {
    list-style: none;
    margin-top: 14px;
    font-family: "Lato", sans-serif;
    font-size: 12.5px;
    color: var(--text-light);
  }
  .contact__list li {
    display: flex;
    align-items: center;
    gap: 5px;
    line-height: 16.5px;
  }
  .contact__icon { width: 10px; height: 10px; flex: none; }
</style>
</head>
<body>
  <section class="card card--front" aria-label="Business card front">
    <div class="brand">
      <span class="brand__square"></span>
      <span class="brand__name">HARWICK PARTNERS</span>
    </div>
    <div class="contact-bar"></div>
    <div class="contact">
      <p class="contact__name">DANIELLE FROST</p>
      <p class="contact__role">Executive Assistant</p>
      <ul class="contact__list">
        <li>
          <svg class="contact__icon" viewBox="0 0 10 10" aria-hidden="true">
            <path d="M1 3.5 Q5 0.5 9 3.5 L8 5 L6.5 4 L6.5 3 Q5 2.5 3.5 3 L3.5 4 L2 5 Z" fill="#22b86b"/>
            <rect x="2" y="5.2" width="6" height="3.5" rx="0.6" fill="#22b86b"/>
          </svg>
          <span>+64 21 473 5162</span>
        </li>
        <li>
          <svg class="contact__icon" viewBox="0 0 10 10" aria-hidden="true">
            <rect x="0.5" y="2" width="9" height="6.5" fill="#22b86b"/>
            <path d="M0.8 2.3 L5 5.8 L9.2 2.3" fill="none" stroke="#1c1b1c" stroke-width="1"/>
          </svg>
          <span>danielf@harwickpartners.co.nz</span>
        </li>
      </ul>
    </div>
  </section>

  <section class="card card--back" aria-label="Business card back">
    <div class="brand">
      <span class="brand__square"></span>
      <span class="brand__name">HARWICK PARTNERS</span>
    </div>
  </section>
</body>
</html>
```